Business card design for Automotive workshop

We need a business card for a new automotive repair and tyre shop called Keelstone Prime Automotive located in New Zealand. We are a clean, modern and fresh workshop and company.

Front needs to feature logo,
my name:
Marlo Fenwicke (director)

Address:
48 Tarn Lane
Harrowby 3627

Phone: 07 594 2713
Mobile: 027 451 9362
Email: office@keelstoneautomotive.example.nz
Website: keelstoneautomotive.example.nz

Back needs to feature an area to write down appointment details, date and time.

Also feature a list of jobs and work we do such as,
Vehicle Servicing
All Mechanical Repairs
Warrant of Fitness
Tyres & Wheel Alignments
Automotive Diagnostics
Automotive Parts & Supplies

```html
<!DOCTYPE html>
<html lang="en">
<head>
<meta charset="utf-8">
<title>Keelstone Prime Automotive – Business Card</title>
<link rel="stylesheet" href="https://fonts.googleapis.com/css2?family=Ubuntu:ital,wght@0,400;0,500;0,700;1,500;1,700&display=swap">
<style>
  :root {
    --stage: #3b3633;
    --card: #121212;
    --panel: #323232;
    --red: #e31b23;
    --white: #ffffff;
    --muted: #d9d9d9;
  }
  * { box-sizing: border-box; margin: 0; padding: 0; }
  html, body { width: 1200px; height: 810px; overflow: hidden; }
  body {
    background: var(--stage);
    font-family: "Ubuntu", Arial, sans-serif;
    color: var(--white);
    position: relative;
  }
  .card {
    position: absolute;
    top: 250px;
    width: 540px;
    height: 310px;
    background: var(--card);
    overflow: hidden;
  }
  .card--back { left: 45px; }
  .card--front { left: 615px; }

  /* Back */
  .appt-title {
    position: absolute; top: 18px; left: 0; width: 100%;
    text-align: center; color: var(--red);
    font-style: italic; font-weight: 500; font-size: 20px;
  }
  .appt-panel {
    position: absolute; top: 52px; left: 40px; width: 460px; height: 112px;
    background: var(--panel);
  }
  .appt-field {
    position: absolute; left: 20px; right: 20px;
    display: flex; align-items: flex-end; gap: 8px;
    font-weight: 700; font-style: italic; font-size: 14px;
  }
  .appt-field--date { top: 24px; }
  .appt-field--time { top: 70px; }
  .appt-field .line { flex: 1; border-bottom: 1.5px dashed var(--muted); margin-bottom: 3px; }
  .works-heading {
    position: absolute; top: 186px; left: 0; width: 100%;
    display: flex; justify-content: center; align-items: center; gap: 14px;
    font-weight: 700; font-style: italic; font-size: 13px;
  }
  .works-heading .rule { width: 90px; height: 2px; background: var(--red); }
  .works-list {
    position: absolute; top: 222px; left: 14px; right: 14px;
    list-style: none; display: grid; grid-template-columns: repeat(3, auto);
    justify-content: center; column-gap: 16px; row-gap: 14px;
    font-size: 12.5px;
  }
  .works-list li { display: flex; align-items: center; gap: 6px; white-space: nowrap; }
  .works-list li::before {
    content: ""; width: 6px; height: 6px; border-radius: 50%; background: var(--red);
  }

  /* Front */
  .brand {
    position: absolute; top: 58px; right: 30px; width: 300px;
    text-align: center; color: var(--white);
    font-weight: 700; font-size: 26px; line-height: 1.1; letter-spacing: 1px;
    text-transform: uppercase;
  }
  .person {
    position: absolute; top: 156px; right: 312px; text-align: right;
  }
  .person-name { color: var(--red); font-weight: 500; font-size: 22px; white-space: nowrap; }
  .person-role { font-size: 14px; margin-top: 6px; }
  .divider {
    position: absolute; top: 155px; left: 244px; width: 1px; height: 76px;
    background: var(--muted);
  }
  .contacts {
    position: absolute; top: 156px; left: 258px; list-style: none;
    font-size: 13px; line-height: 19px;
  }
  .contacts li { display: flex; align-items: center; gap: 7px; white-space: nowrap; }
  .contacts svg { width: 10px; height: 10px; flex: none; }
  .address-band {
    position: absolute; top: 246px; left: 0; width: 100%; height: 34px;
    background: var(--red);
    display: flex; align-items: center; padding-left: 150px;
    font-size: 14px; white-space: nowrap;
  }
</style>
</head>
<body>

<section class="card card--back" aria-label="Business card back">
  <h2 class="appt-title">Appointment Details</h2>
  <div class="appt-panel">
    <div class="appt-field appt-field--date"><span>Date</span><span class="line"></span></div>
    <div class="appt-field appt-field--time"><span>Time</span><span class="line"></span></div>
  </div>
  <div class="works-heading"><span class="rule"></span><span>Our Works</span><span class="rule"></span></div>
  <ul class="works-list">
    <li>Vehicle Servicing</li>
    <li>Warrant of Fitness</li>
    <li>Automotive Parts &amp; Supplies</li>
    <li>Automotive Diagnostics</li>
    <li>Tyres &amp; Wheel Alignments</li>
    <li>All Mechanical Repairs</li>
  </ul>
</section>

<section class="card card--front" aria-label="Business card front">
  <div class="brand">Keelstone Prime Automotive</div>
  <div class="person">
    <div class="person-name">Marlo Fenwicke</div>
    <div class="person-role">Director</div>
  </div>
  <span class="divider"></span>
  <ul class="contacts">
    <li>
      <svg viewBox="0 0 10 10"><path d="M2 0.5 L4 3 L3 4.2 Q4 6.2 5.8 7 L7 6 L9.5 8 L8.3 9.5 Q3 9 0.5 2 Z" fill="var(--red)"/></svg>
      07 594 2713
    </li>
    <li>
      <svg viewBox="0 0 10 10"><rect x="2.5" y="0.5" width="5" height="9" rx="1" fill="none" stroke="var(--red)" stroke-width="1.2"/><circle cx="5" cy="8" r="0.6" fill="var(--red)"/></svg>
      027 451 9362
    </li>
    <li>
      <svg viewBox="0 0 10 10"><rect x="0.5" y="2" width="9" height="6.5" fill="var(--red)"/><path d="M0.5 2 L5 5.5 L9.5 2" fill="none" stroke="var(--card)" stroke-width="0.9"/></svg>
      office@keelstoneautomotive.example.nz
    </li>
    <li>
      <svg viewBox="0 0 10 10"><circle cx="5" cy="5" r="4.4" fill="none" stroke="var(--red)" stroke-width="1.1"/><path d="M0.6 5 H9.4 M5 0.6 Q2 5 5 9.4 M5 0.6 Q8 5 5 9.4" fill="none" stroke="var(--red)" stroke-width="0.8"/></svg>
      keelstoneautomotive.example.nz
    </li>
  </ul>
  <div class="address-band">48 Tarn Lane Harrowby 3627</div>
</section>

</body>
</html>
```